Revamp of existing namecard

Existingly, i've got a namecard that i would like to retain the main design. but there are some changes in my company and i would need to do some amendments to it.

We are a money transfer and money exchange company.
I need 2 different types of name card.
1. For individual name cards
the front to put the following:
Company name and logo
English Name, Chinese Name appointment
Mobile Number, Email and Website.
2 License number under the logo and name

the back of the name card to put
8 address: 7 Singapore and 1 Hong Kong branch addresses
8 Mobile Number of the corresponding addresses.

We would like to retain the name card front design
the name card back design can change but color to retain.

2nd name card is generic name card
Front:
Company name and logo
Branch Mobile Number, Branch Address, Email and Website.

Industry/Entity Type

remittance and money exchange

Contact Information for Business Card

I need 2 different types of name card. 1. For individual name cards the front to put the following: Company name and logo English Name, Chinese Name appointment Mobile Number, Email and Website. 2 License number under the logo and name the back of the name card to put 8 address: 7 Singapore and 1 Hong Kong branch addresses 8 Mobile Number of the corresponding addresses. We would like to retain the name card front design the name card back design can change but color to retain. 2nd name card is generic name card Front: the front to put the following: Company name and logo Branch Mobile Number, Branch Address, Email and Website. 2 License number under the logo and name

Requirements
Must have
• I need 2 different types of name card. 1. For individual name cards the front to put the following: Company name and logo English Name, Chinese Name appointment Mobile Number, Email and Website. 2 License number under the logo and name the back of the name card to put 8 address: 7 Singapore and 1 Hong Kong branch addresses 8 Mobile Number of the corresponding addresses. We would like to retain the name card front design the name card back design can change but color to retain. 2nd name card is generic name card Front: the front to put the following: Company name and logo Branch Mobile Number, Branch Address, Email and Website. 2 License number under the logo and name
Nice to have
• use back color code

```html
<!DOCTYPE html>
<html lang="en">
<head>
<meta charset="utf-8">
<title>Orivant – Branch Name Card</title>
<link rel="stylesheet" href="https://fonts.googleapis.com/css2?family=Montserrat:wght@400;500;600;700&display=swap">
<style>
  :root {
    --page-bg: #e9eaec;
    --card-bg: #ffffff;
    --ink: #1f2b38;
    --ink-soft: #2d3a48;
    --accent: #3a9fbd;
    --map-tone: #e4e6e9;
    --map-edge: #f6f7f8;
  }
  * { margin: 0; padding: 0; box-sizing: border-box; }
  html, body {
    width: 1200px; height: 799px; overflow: hidden;
    background: var(--page-bg);
    font-family: "Montserrat", sans-serif;
    color: var(--ink);
  }
  .card {
    position: absolute; left: 151px; top: 127px;
    width: 897px; height: 544px;
    background: var(--card-bg);
    box-shadow: 0 10px 30px rgba(0,0,0,.12);
    overflow: hidden;
  }
  .world-map {
    position: absolute; left: 32px; top: 15px; width: 829px; height: 462px;
    background: radial-gradient(ellipse at 55% 45%, var(--map-tone) 0%, var(--map-edge) 65%, transparent 85%);
    opacity: .9;
  }
  .brand { position: absolute; left: 447px; top: 78px; }
  .brand-row { display: flex; align-items: center; gap: 14px; }
  .brand-dot { width: 46px; height: 46px; border-radius: 50%; background: var(--accent); }
  .brand-name { font-size: 50px; font-weight: 600; letter-spacing: 1px; line-height: 1; color: var(--ink); }
  .license { margin: 6px 0 0 112px; font-size: 19px; font-weight: 500; letter-spacing: 1px; color: var(--ink); }
  .branch { position: absolute; left: 36px; top: 205px; }
  .branch-title { display: flex; align-items: center; gap: 6px; font-size: 46px; line-height: 1; color: var(--ink); }
  .branch-title b { font-weight: 700; }
  .branch-title span { font-weight: 500; }
  .branch-label { margin-left: 54px; font-size: 18px; color: var(--accent); }
  .address { position: absolute; left: 53px; top: 306px; font-size: 21px; line-height: 32px; font-weight: 500; color: var(--ink-soft); }
  .contacts { position: absolute; left: 531px; top: 258px; list-style: none; font-size: 22px; font-weight: 500; color: var(--ink-soft); }
  .contacts li { display: flex; align-items: center; gap: 8px; height: 35.5px; letter-spacing: .5px; }
  .contacts svg { width: 20px; height: 20px; fill: none; stroke: var(--accent); stroke-width: 2; }
</style>
</head>
<body>
  <div class="card">
    <div class="world-map" role="img" aria-label="Faint dotted world map in light grey"></div>

    <div class="brand">
      <div class="brand-row">
        <div class="brand-dot"></div>
        <div class="brand-name">ORIVANT</div>
      </div>
      <div class="license">04183627 | 05291846</div>
    </div>

    <div class="branch">
      <div class="branch-title">
        <svg width="36" height="46" viewBox="0 0 24 32"><path d="M12 1C6 1 2 5.5 2 11c0 7.5 10 19 10 19s10-11.5 10-19C22 5.5 18 1 12 1z" fill="#3a9fbd"/><circle cx="12" cy="11" r="4" fill="#fff"/></svg>
        <b>Pasir</b> <span>Ris</span>
      </div>
      <div class="branch-label">branch</div>
    </div>

    <div class="address">
      <p>Unit 1615, 16th Floor</p>
      <p>Harbour Crest Tower</p>
      <p>18 Kellet Lane, Causeway Bay</p>
    </div>

    <ul class="contacts">
      <li><svg viewBox="0 0 20 20"><rect x="5" y="2" width="10" height="16" rx="2"/><line x1="9" y1="15" x2="11" y2="15"/></svg>+852 9412 3085</li>
      <li><svg viewBox="0 0 20 20"><path d="M4 2l3 0 2 4-2 2c1 2 3 4 5 5l2-2 4 2v3c0 1-1 2-2 2C9 18 2 11 2 4c0-1 1-2 2-2z" fill="#3a9fbd" stroke="none"/></svg>+852 9530 4718</li>
      <li><svg viewBox="0 0 20 20"><rect x="2" y="4" width="16" height="12" fill="#3a9fbd" stroke="none"/><path d="M2 4l8 7 8-7" stroke="#fff"/></svg>kelvin@orivant.com.hk</li>
      <li><svg viewBox="0 0 20 20"><circle cx="10" cy="10" r="8"/><ellipse cx="10" cy="10" rx="3.5" ry="8"/><line x1="2" y1="10" x2="18" y2="10"/></svg>www.orivant.com.hk</li>
    </ul>
  </div>
</body>
</html>
```